BRAMBLEFORD CONSTRUCTIONS B-Card

I currently have a b-card design but will be removing the image (tree) from the logo and have text only.
I want the card to be classy and strong within the building and construction industry.
I will be using Spot UV on the cards as per the attached examples. I will also send through some sketched ideas that I have in mind.
The color blue is similar to the image (No. 6) attached images

Target Market(s)

middle to maturre aged.
Home Owners / Renovators and Builders

Industry/Entity Type

Construction

Contact Information for Business Card

BRAMBLEFORD CONSTRUCTIONS
Name: Gareth Pennick
Title: Project Manager
Mobile: 0427 351 804
Office: (08) 9316 5172
Address: 47C Corvell Street, Tarlow XA 5173
Email: info@bramblefordhomes.com.au
PO Box: 3817 Tarlow XA 5178

Colors
0592cd
33a6d7
85cae6
1b1b1b

Requirements
Must have
• 1. It must have spot UV on the front of card, maybe back of card too
• 2. I really like the blue on image 6. (or at least a really cool electric blue against the charcoal grey background)
• 3. The font must be slimline and modern. Easy to read
• 4. There must be no black used on the card... Only greys and dark charcoal greys
• 5. Use only the text from the logo "Brambleford Constructions" Not the image of the tree. I am wanting the b-cards to be more masculine.
Nice to have
• 1. I like the design concept on image 6. but happy to see what else you can do with the Spot UV
• 2. Unless you have a really cool idea of the image of the tree (from previous logo) Spot UV somewhere in the design concept thats original and different then I am keen to see what you come up with
• 3. Try changing the color of the logo eg. full white or Blue and white
• 4. Another option is to have the Brambleford Logo on the front of card with the spot UV in the background of text which we specialise in eg, Roofing, Ceiling, Insulation, Gutter Guards, Electrical, Insurance etc and we can add or reduce items as required. Similar to image 12.
Should not have
• Do not include the image of the tree from previous logo. unless you have a really cool idea of Spot UV somewhere in the design concept thats original and different.

```html
<!DOCTYPE html>
<html lang="en">
<head>
<meta charset="utf-8">
<title>Brambleford Constructions – Business Card</title>
<link rel="stylesheet" href="https://fonts.googleapis.com/css2?family=Open+Sans:wght@400;600;700&family=Montserrat:wght@300;600&display=swap">
<style>
  :root {
    --blue-deep: #0592cd;
    --blue: #33a6d7;
    --blue-card: #2fa5da;
    --blue-light: #85cae6;
    --charcoal: #1b1b1b;
    --charcoal-pattern: #1f2a30;
    --white: #ffffff;
    --backdrop: #ecebe9;
  }
  * { box-sizing: border-box; margin: 0; padding: 0; }
  html, body {
    width: 1200px;
    height: 900px;
    overflow: hidden;
  }
  body {
    position: relative;
    background: var(--backdrop);
    font-family: "Open Sans", Arial, sans-serif;
  }

  .card {
    position: absolute;
    width: 556px;
    height: 342px;
    overflow: hidden;
    box-shadow: 0 6px 18px rgba(0,0,0,0.18);
  }

  /* Front */
  .card--front {
    left: 238px;
    top: 62px;
    background: var(--blue-card);
    color: var(--white);
  }
  .front__name {
    position: absolute;
    left: 32px;
    top: 38px;
    font-size: 18px;
    font-weight: 600;
    line-height: 22px;
  }
  .front__title {
    position: absolute;
    left: 32px;
    top: 60px;
    font-size: 14px;
    font-weight: 400;
  }
  .front__address {
    position: absolute;
    left: 32px;
    top: 193px;
    font-size: 14px;
    line-height: 20px;
  }
  .front__address strong { font-weight: 700; }
  .front__phones {
    position: absolute;
    left: 32px;
    top: 267px;
    list-style: none;
    font-size: 14px;
    line-height: 20px;
  }
  .front__phones li {
    display: flex;
    align-items: center;
    gap: 7px;
  }
  .front__phones svg { width: 12px; height: 12px; fill: var(--white); }
  .front__artwork {
    position: absolute;
    left: 258px;
    top: 0;
    width: 298px;
    height: 342px;
    background: radial-gradient(ellipse at 60% 45%, #ffffff 0%, #f2f9fd 55%, #dcf0f9 100%);
    border-radius: 48% 0 0 42% / 50% 0 0 50%;
  }

  /* Back */
  .card--back {
    left: 458px;
    top: 518px;
    width: 560px;
    background: var(--charcoal);
  }
  .back__pattern {
    position: absolute;
    inset: 0;
    background: radial-gradient(ellipse at 15% 50%, var(--charcoal-pattern) 0%, transparent 45%),
                radial-gradient(ellipse at 85% 50%, var(--charcoal-pattern) 0%, transparent 45%),
                var(--charcoal);
  }
  .back__logo {
    position: absolute;
    left: 0;
    right: 0;
    top: 140px;
    text-align: center;
    font-family: "Montserrat", Arial, sans-serif;
    color: var(--blue);
  }
  .back__logo-name {
    display: block;
    font-size: 40px;
    font-weight: 600;
    line-height: 44px;
    letter-spacing: -0.5px;
  }
  .back__logo-type {
    display: block;
    font-size: 19px;
    font-weight: 300;
    letter-spacing: 9.6px;
    margin-left: 9.6px;
    margin-top: 2px;
  }
</style>
</head>
<body>

  <section class="card card--front" aria-label="Business card front">
    <div class="front__artwork" role="img" aria-label="Large white illustration of a tree with leaves and roots"></div>
    <p class="front__name">Gareth Pennick</p>
    <p class="front__title">Project Manager</p>
    <p class="front__address">
      47C Corvell Street,<br>
      Tarlow XA 5173<br>
      <strong>PO Box:</strong> 3817 Tarlow XA 5178
    </p>
    <ul class="front__phones">
      <li>
        <svg viewBox="0 0 12 12" aria-hidden="true"><path d="M3.5 0h5a1 1 0 0 1 1 1v10a1 1 0 0 1-1 1h-5a1 1 0 0 1-1-1V1a1 1 0 0 1 1-1zm.5 1.5v7.5h4V1.5zM6 9.8a.7.7 0 1 0 0 1.4.7.7 0 0 0 0-1.4z"/></svg>
        0427 351 804
      </li>
      <li>
        <svg viewBox="0 0 12 12" aria-hidden="true"><path d="M2.4 0.6l1.8 1.8c.3.3.3.8 0 1.1l-.9.9c.8 1.6 2 2.8 3.6 3.6l.9-.9c.3-.3.8-.3 1.1 0l1.8 1.8c.3.3.3.8 0 1.1l-1 1c-.6.6-1.5.7-2.2.3C4.8 10 2 7.2.7 4.5.3 3.8.4 2.9 1 2.3l1-1c.4-.4.9-.4 1.4-.7z"/></svg>
        (08) 9316 5172
      </li>
    </ul>
  </section>

  <section class="card card--back" aria-label="Business card back">
    <div class="back__pattern" role="img" aria-label="Faint dark repeating tree pattern"></div>
    <p class="back__logo">
      <span class="back__logo-name">BRAMBLEFORD</span>
      <span class="back__logo-type">CONSTRUCTIONS</span>
    </p>
  </section>

</body>
</html>
```